home accents e-commerce website

I'd like a professional simple website designed where I can sell my home goods. I already have my domain name registered. I need the website to accept credit card payments and Monvex. It should have a shopping cart option and calculate sales tax and shipping costs on merchandise automatically.

I'll be taking photographs of the merchandise and writing product descriptions myself. (I'm not a professional photographer, so these photos probably won't look too polished. If you can help me make them look better, that'd be great). As I add new merchandise in the future, I'd like an option where I can log in to the back end myself and add pictures/product descriptions. And take old products down as they sell out. So the website needs to be user-friendly for me, even though I'm completely web design illiterate!

I'd like a creative, talented person who can create a whimsical, cute website. Nothing too corporate-looking.

Thank you!

Target Market(s)

women, online shoppers, New York City-area, (ship products to the United States only)

Industry/Entity Type

Home And Garden

Coding

Coded - Design and coding required

Number of Pages Required

1 page

Font styles to use
Sans Serif

Colors
0355a3
ffffff

Requirements
Must have
• shopping cart feature
• safe, secure credit card and Monvex payments
• ability for me to go in and add new products and take down old/sold products
Nice to have
• whimsical, cute design
Should not have
• too corporate-looking

```html
<!DOCTYPE html>
<html lang="en">
<head>
<meta charset="utf-8">
<title>Lumora Home Goods</title>
<link href="https://fonts.googleapis.com/css2?family=Lato:wght@400;700;900&display=swap" rel="stylesheet">
<style>
:root{
  --brand:#0355a3;
  --navy:#0d1f6e;
  --white:#ffffff;
  --ink:#222222;
  --muted:#555555;
  --line:#e2e2e2;
  --tile:#efefef;
  --footer:#f0f0f0;
}
*{box-sizing:border-box;margin:0;padding:0}
html,body{width:1200px;height:3169px;overflow:hidden}
body{font-family:'Lato',sans-serif;color:var(--ink);background:var(--white);position:relative}
.wrap{position:absolute;left:118px;width:957px}
.btn{display:inline-block;background:var(--brand);color:var(--white);font-size:11px;font-weight:700;text-transform:uppercase;padding:5px 12px;letter-spacing:.3px}
.section-title{font-size:21px;font-weight:900;color:var(--navy);text-transform:uppercase;letter-spacing:.3px}

/* header */
.site-header{position:absolute;top:0;left:0;width:1200px;height:120px}
.wordmark{position:absolute;left:131px;top:24px;color:var(--navy)}
.wordmark .name{font-size:50px;font-weight:900;line-height:48px;letter-spacing:1px}
.wordmark .tag{font-size:17px;letter-spacing:5px;text-transform:uppercase;margin-top:2px}
.follow{position:absolute;left:748px;top:26px;display:flex;align-items:center;gap:6px;font-size:12px}
.dot{width:22px;height:22px;border-radius:50%;color:var(--white);font-size:11px;font-weight:700;display:flex;align-items:center;justify-content:center}
.dot.a{background:#3b5a9a}.dot.b{background:#1d9ce0}.dot.c{background:#dc5a44}
.cart{position:absolute;left:975px;top:27px;display:flex;align-items:center;gap:10px;font-size:12px}
.main-nav{position:absolute;right:132px;top:80px;display:flex;gap:46px;font-size:14px}

/* hero */
.hero{position:absolute;top:120px;left:0;width:1200px;height:567px;background:linear-gradient(180deg,#e9e9e7 0%,#dcdcda 55%,#c9c9c7 100%)}
.hero-copy{position:absolute;left:386px;top:135px;color:var(--navy)}
.hero-copy .pre{font-size:23px;font-weight:700;line-height:24px;color:#1a1a1a}
.hero-copy h1{font-size:46px;font-weight:400;line-height:52px;letter-spacing:1px}
.hero-copy h1 b{font-weight:900}
.hero-copy .btn{position:absolute;left:262px;top:103px;font-size:15px;padding:8px 20px;background:var(--navy)}
.sofa{position:absolute;left:326px;top:275px;width:532px;height:240px;border-radius:20px;background:linear-gradient(180deg,#d0d0ce,#b8b8b6)}
.pager{position:absolute;top:513px;left:549px;display:flex;gap:14px}
.pager span{width:8px;height:8px;border-radius:50%;background:var(--white)}

/* sidebar */
.search{position:absolute;left:118px;top:746px;width:243px;height:44px;border:1px solid var(--line);display:flex;align-items:center;gap:10px;padding-left:14px;font-size:9px;color:var(--muted);letter-spacing:.5px}
.categories{position:absolute;left:118px;top:811px;width:243px;height:596px;border:1px solid var(--line);padding:20px 22px}
.categories h3{font-size:15px;font-weight:900;color:var(--navy);margin-bottom:12px}
.categories li{list-style:none;display:flex;align-items:center;gap:16px;height:57.5px;border-bottom:1px solid var(--line);font-size:13px;color:#333}
.categories li:last-child{border-bottom:0}
.categories i{width:13px;height:13px;background:#555;border-radius:2px;display:block}

/* featured */
.featured-title{position:absolute;left:389px;top:752px}
.product-grid{position:absolute;left:389px;top:809px;width:686px;display:grid;grid-template-columns:repeat(3,226px);gap:6px}
.product{height:296px;background:var(--tile);border:1px solid var(--line);position:relative;padding:0 26px}
.product .photo{position:absolute;left:40px;top:18px;width:146px;height:170px;border-radius:6px}
.product .name{position:absolute;left:26px;top:202px;font-size:13px}
.product .price{position:absolute;left:26px;top:218px;font-size:17px;font-weight:700;color:var(--brand)}
.product .btn{position:absolute;left:26px;top:250px;font-size:10px;padding:4px 10px}

/* floors banner */
.floors{position:absolute;left:118px;top:1447px;width:957px;height:262px;background:linear-gradient(100deg,#5a3a24 0%,#8a6040 40%,#a57855 65%,#5e3e28 100%);color:var(--white)}
.floors .left{position:absolute;left:82px;top:78px}
.floors .left small{font-size:27px;font-weight:900;display:block;line-height:28px}
.floors .left strong{font-size:62px;font-weight:900;line-height:66px}
.floors .right{position:absolute;left:742px;top:112px}
.floors .right small{font-size:15px;font-weight:700}
.floors .right strong{display:block;font-size:60px;font-weight:900;line-height:62px}
.floors .btn{position:absolute;left:748px;top:214px}

/* new products */
.new-title{position:absolute;left:118px;top:1755px}
.arrows{position:absolute;left:1032px;top:1756px;display:flex;gap:14px}
.new-box{position:absolute;left:118px;top:1806px;width:957px;height:334px;border:1px solid var(--line)}
.new-box .photo{position:absolute;left:40px;top:50px;width:520px;height:240px;border-radius:6px;background:linear-gradient(110deg,#f3b4c6 0%,#f5a13a 30%,#5bc6e0 55%,#d7e24a 80%,#8c7ac0 100%)}
.new-box .info{position:absolute;left:617px;top:44px;width:300px}
.new-box h4{font-size:15px;font-weight:900;color:var(--navy)}
.new-box p{font-size:12px;line-height:18px;color:#444;margin-top:12px;text-align:justify}
.new-box .from{font-size:11px;font-weight:700;margin-top:30px}
.new-box .price{font-size:29px;font-weight:900;color:var(--brand)}
.new-box .btn{margin-top:20px}

/* blog */
.blog-title{position:absolute;left:0;width:1200px;text-align:center;top:2205px}
.blog{position:absolute;left:118px;top:2286px;display:flex;gap:13px}
.post{width:310px;text-align:center}
.post .photo{height:180px}
.post h5{font-size:16px;font-weight:400;margin:28px 0 14px}

/* perks */
.perks{position:absolute;left:118px;top:2637px;display:flex;gap:13px}
.perk{width:310px;height:72px;background:var(--brand);color:var(--white);display:flex;align-items:center;padding-left:30px;gap:28px}
.perk strong{display:block;font-size:17px;font-weight:900}
.perk span{font-size:11px}

/* footer */
.site-footer{position:absolute;top:2783px;left:0;width:1200px;height:386px;background:var(--footer)}
.site-footer .wordmark{left:120px;top:60px}
.foot-follow{position:absolute;left:120px;top:202px;width:212px;border-top:1px solid #ccc;border-bottom:1px solid #ccc;height:70px;display:flex;align-items:center;gap:8px;font-size:11px;font-weight:900;color:var(--navy)}
.foot-follow .dot{width:28px;height:28px;font-size:13px}
.copy{position:absolute;left:120px;top:322px;font-size:10px;color:#555}
.col{position:absolute;top:60px}
.col h6{font-size:11px;font-weight:900;color:var(--navy);margin-bottom:14px}
.col li{list-style:none;font-size:11px;line-height:28px;color:#333}
.newsletter{position:absolute;left:806px;top:60px;width:270px}
.newsletter h6{font-size:11px;font-weight:900;color:var(--navy)}
.newsletter .field{margin-top:18px;height:48px;background:var(--white);border:1px solid #ddd;display:flex;align-items:center;gap:12px;padding-left:24px;font-size:11px}
.newsletter .btn{position:absolute;right:0;top:108px;font-size:15px;padding:10px 18px;background:var(--navy)}
.pay{position:absolute;left:806px;top:280px;width:270px;border-top:1px solid #ccc;padding-top:32px;display:flex;gap:4px;justify-content:flex-end}
.pay span{background:var(--white);border:1px solid #ccc;font-size:9px;font-weight:700;color:var(--navy);padding:6px 4px;width:48px;text-align:center}
</style>
</head>
<body>

<header class="site-header">
  <div class="wordmark"><div class="name">lumora</div><div class="tag">Home Goods</div></div>
  <div class="follow">Follow us on : <span class="dot a">P</span><span class="dot b">C</span><span class="dot c">G</span></div>
  <div class="cart">
    <svg width="18" height="15" viewBox="0 0 18 15"><path d="M0 1h3l2.5 9h9L17 3H4.5" fill="none" stroke="#111" stroke-width="2"/><circle cx="6.5" cy="13" r="1.6"/><circle cx="13.5" cy="13" r="1.6"/></svg>
    My Cart (0)
  </div>
  <nav class="main-nav"><span>About Lumora</span><span>How does this craziness work?</span><span>Contact</span></nav>
</header>

<section class="hero">
  <div class="sofa" role="img" aria-label="Grey sofa with chevron throw pillows in a bright living room"></div>
  <div class="hero-copy">
    <div class="pre">GET 15%<br>DISCOUNT</div>
    <h1>THROW <b>PILLOWS</b></h1>
    <span class="btn">Shop Now</span>
  </div>
  <div class="pager"><span></span><span></span><span></span><span></span><span></span></div>
</section>

<div class="search">
  <svg width="10" height="10" viewBox="0 0 10 10"><circle cx="4" cy="4" r="3" fill="none" stroke="#555" stroke-width="1.4"/><path d="M6.3 6.3 9 9" stroke="#555" stroke-width="1.4"/></svg>
  SEARCH BY PRODUCTS
</div>

<aside class="categories">
  <h3>SHOP BY CATEGORIES</h3>
  <ul>
    <li><i style="border-radius:50% 50% 40% 40%"></i>Vases</li>
    <li><i></i>Throw Pillows</li>
    <li><i></i>Blankets and Throws</li>
    <li><i style="transform:rotate(45deg)"></i>For Your Floors</li>
    <li><i></i>For Your Walls</li>
    <li><i style="height:8px"></i>For Your Table</li>
    <li><i></i>For Your Bedside</li>
    <li><i></i>Let THere Be Light</li>
    <li><i></i>Put Your Feet Up</li>
  </ul>
</aside>

<h2 class="section-title featured-title">Featured Products</h2>
<div class="product-grid">
  <div class="product"><div class="photo" role="img" aria-label="Teal vase with pink roses" style="background:radial-gradient(circle at 50% 30%,#e27fb0,#1f8a86 70%,var(--tile) 72%)"></div><div class="name">Vases</div><div class="price">$15.99</div><span class="btn">Shop Now</span></div>
  <div class="product"><div class="photo" role="img" aria-label="Rolled blue blanket" style="background:radial-gradient(ellipse at 50% 50%,#4a6db8,#2c4a8f 60%,var(--tile) 62%)"></div><div class="name">Blankets</div><div class="price">$15.99</div><span class="btn">Shop Now</span></div>
  <div class="product"><div class="photo" role="img" aria-label="Grey office desk with drawers" style="background:linear-gradient(180deg,var(--tile) 20%,#d8d8d6 22%,#bfbfbd 80%,var(--tile) 82%)"></div><div class="name">Vases</div><div class="price">$15.99</div><span class="btn">Shop Now</span></div>
  <div class="product"><div class="photo" role="img" aria-label="Table lamp with floral shade" style="background:linear-gradient(180deg,#f1d873 0%,#d9a24a 50%,#b87a3e 90%,var(--tile) 92%)"></div><div class="name">Vases</div><div class="price">$15.99</div><span class="btn">Shop Now</span></div>
  <div class="product"><div class="photo" role="img" aria-label="Gold ornate wall clock" style="background:radial-gradient(circle,#f6e6a8,#d4a017 55%,var(--tile) 60%)"></div><div class="name">Blankets</div><div class="price">$15.99</div><span class="btn">Shop Now</span></div>
  <div class="product"><div class="photo" role="img" aria-label="Patterned hanging pendant lamp" style="background:radial-gradient(ellipse at 50% 60%,#e6b3a6,#c8504a 50%,var(--tile) 60%)"></div><div class="name">Vases</div><div class="price">$15.99</div><span class="btn">Shop Now</span></div>
</div>

<section class="floors" role="img" aria-label="Fan of wooden floor plank samples">
  <div class="left"><small>SHOP BY</small><strong>FLOORS</strong></div>
  <div class="right"><small>STARTING FROM</small><strong>$59.99</strong></div>
  <span class="btn">Shop Now</span>
</section>

<h2 class="section-title new-title">New Products</h2>
<div class="arrows">
  <svg width="10" height="16" viewBox="0 0 10 16"><path d="M8 1 2 8l6 7" fill="none" stroke="#666" stroke-width="1.6"/></svg>
  <svg width="10" height="16" viewBox="0 0 10 16"><path d="M2 1l6 7-6 7" fill="none" stroke="#666" stroke-width="1.6"/></svg>
</div>
<section class="new-box">
  <div class="photo" role="img" aria-label="Stack of colourful patterned cushions"></div>
  <div class="info">
    <h4>PILLOW</h4>
    <p>Lorem Ipsum is simply dummy text of the printing and typesetting industry. Lorem Ipsum has been the industry's standard dummy text ever since the 1500s, when an unknown printer took a galley of type and scrambled it to make a type specimen</p>
    <div class="from">STARTING FROM</div>
    <div class="price">$52.99</div>
    <span class="btn">Shop Now</span>
  </div>
</section>

<h2 class="section-title blog-title">From The Blog</h2>
<div class="blog">
  <article class="post"><div class="photo" role="img" aria-label="Yellow sofa in a living room" style="background:linear-gradient(180deg,#cfcfc6 0%,#b9b4a8 55%,#e6d12a 70%,#8a8478 100%)"></div><h5>Lorem Ipsum is simply dummy</h5><span class="btn">Read More</span></article>
  <article class="post"><div class="photo" role="img" aria-label="Red embroidered cushions at a market stall" style="background:linear-gradient(160deg,#3a3a52 0%,#a8242c 50%,#4f3a6a 100%)"></div><h5>There are many variations</h5><span class="btn">Read More</span></article>
  <article class="post"><div class="photo" role="img" aria-label="Black painted vase on a shelf" style="background:linear-gradient(90deg,#f2f2f2 0%,#d9d6d0 40%,#1c1c1c 60%,#c9c4bb 100%)"></div><h5>But I must explain to you how</h5><span class="btn">Read More</span></article>
</div>

<div class="perks">
  <div class="perk">
    <svg width="40" height="26" viewBox="0 0 40 26"><rect x="1" y="3" width="24" height="16" fill="#fff"/><path d="M25 8h8l5 6v5H25z" fill="#fff"/><circle cx="9" cy="21" r="3.5" fill="#fff" stroke="#0355a3" stroke-width="1.5"/><circle cx="31" cy="21" r="3.5" fill="#fff" stroke="#0355a3" stroke-width="1.5"/></svg>
    <div><strong>FREE SHIPPING</strong><span>Lorem Ipsum is simply</span></div>
  </div>
  <div class="perk">
    <svg width="28" height="26" viewBox="0 0 28 26"><rect x="1" y="11" width="6" height="14" fill="#fff"/><path d="M9 12 15 1c3 0 4 2 3 6l-1 3h8c2 0 3 2 2 4l-3 9c-1 2-2 2-4 2H9z" fill="#fff"/></svg>
    <div><strong>30 DAYS GUARANTEE</strong><span>Lorem Ipsum is simply</span></div>
  </div>
  <div class="perk">
    <svg width="28" height="26" viewBox="0 0 28 26"><path d="M3 16V13a11 11 0 0 1 22 0v3" fill="none" stroke="#fff" stroke-width="3"/><rect x="1" y="14" width="7" height="11" rx="2" fill="#fff"/><rect x="20" y="14" width="7" height="11" rx="2" fill="#fff"/></svg>
    <div><strong>24/7 SUPPORT</strong><span>Lorem Ipsum is simply</span></div>
  </div>
</div>

<footer class="site-footer">
  <div class="wordmark"><div class="name">lumora</div><div class="tag">Home Goods</div></div>
  <div class="foot-follow">FOLLOW US ON <span class="dot a">P</span><span class="dot b">C</span><span class="dot c">G</span></div>
  <div class="copy">Copyrights @ 2017 All Rights Reserved</div>
  <div class="col" style="left:389px"><h6>MENU</h6><ul><li>About lumora</li><li>How does this craziness work?</li><li>Contact us</li></ul></div>
  <div class="col" style="left:623px"><h6>CATEGORIES</h6><ul><li>Vases</li><li>Throw Pillows</li><li>Blankets and Throws</li><li>For Your Floors</li><li>For Your Walls</li><li>For Your Table</li><li>For Your Bedside</li><li>Let THere Be Light</li><li>Put Your Feet Up</li></ul></div>
  <div class="newsletter">
    <h6>NEWSLETTER SIGNUP!</h6>
    <div class="field"><svg width="12" height="9" viewBox="0 0 12 9"><rect x=".5" y=".5" width="11" height="8" fill="none" stroke="#333"/><path d="M.5.5 6 5l5.5-4.5" fill="none" stroke="#333"/></svg>E mail id</div>
    <span class="btn">Signup!</span>
  </div>
  <div class="pay"><span>Monvex</span><span>Cardora</span><span>Vexa</span><span>Amerix</span><span>Findly</span></div>
</footer>

</body>
</html>
```